Real Estate Company Looking for Business Card Designs for 3 Executives

Hello!
Thanks so much for considering our project! We are a real estate investment company located in Edmonton, Alberta called Bellhaven Group of Companies. We invest/develop both commercial and residential real estate and are looking to create 3 DOUBLE-SIDED business cards for 3 top executives in the company! (for some reason it won't let us select the double-sided option, but yes, the cards are double sided and would be happy to tip extra)

We have certain guidelines that we want our business cards to for sure follow - the back of the Business card has to be the Black Background Version of the Logo which has already been designed and linked as a file (first file). We want the entire back of the card to simply just be the black background logo. In terms of the front of the card, would like to see a smaller version of the white background logo (linked as the second file) in the top left hand corner - of course, feel free to get creative and we can make revisions together along the way! and Then after that, just text. We want the card to be sharp, clean, easy on the eyes and highly professional looking. We would like the card to include the Full name of the Company (Bellhaven Group of Companies), Name of the Person, Title, Phone, Email. If possible please provide the front part of the card for 3 people:

1) Bellhaven Group of Companies, Liora Quenby, Chief Financial Officer, 780-555-0142, lioraquenby@bellhavengroup.example

2) Bellhaven Group of Companies, Tobias Quenby, Chief Executive Officer, 780-555-0187, tobiasquenby@bellhavengroup.example

3) Bellhaven Group of Companies, Rui Delcourt, Chief Operations Officer, 587-555-0163, ruidelcourt@bellhavengroup.example

Thank you so much for considering our project & we look forward to seeing your designs!

```html
<!DOCTYPE html>
<html lang="en">
<head>
<meta charset="utf-8">
<title>Bellhaven Business Card</title>
<link href="https://fonts.googleapis.com/css2?family=Arimo:wght@400;700&display=swap" rel="stylesheet">
<style>
  :root {
    --page: #1f1f1f;
    --card-black: #0b0b0b;
    --paper-white: #ffffff;
    --ink-black: #111111;
    --gloss: #3c3c3c;
    --text-light: #f2f2f2;
  }
  * { margin: 0; padding: 0; box-sizing: border-box; }
  html, body {
    width: 1200px; height: 1015px; overflow: hidden;
    background: var(--page);
    font-family: "Arimo", Arial, sans-serif;
  }
  .sheet {
    width: 1200px; height: 1015px;
    display: flex; flex-direction: column;
    align-items: center; justify-content: center; gap: 44px;
  }
  .card {
    position: relative;
    width: 760px; height: 434px;
    background: var(--card-black);
    overflow: hidden;
    box-shadow: 0 10px 30px rgba(0,0,0,0.55);
  }

  /* Back side */
  .card-back .wordmark {
    position: absolute; inset: 0;
    display: flex; align-items: center; justify-content: center;
    font-size: 46px; font-weight: 400; letter-spacing: 0.32em;
    color: var(--gloss);
    padding-left: 0.32em;
  }

  /* Front side */
  .front-shape { position: absolute; inset: 0; }
  .card-front .wordmark {
    position: absolute; left: 455px; top: 122px; width: 330px;
    text-align: center;
    font-size: 30px; font-weight: 400; letter-spacing: 0.28em;
    color: var(--ink-black);
  }
  .identity { position: absolute; left: 52px; top: 200px; color: var(--text-light); }
  .identity .person-name {
    font-size: 28px; font-weight: 700; letter-spacing: 0.02em; line-height: 1;
  }
  .identity .person-title { font-size: 19px; font-weight: 400; margin-top: 4px; }
  .contacts {
    position: absolute; left: 52px; bottom: 40px;
    list-style: none; color: var(--text-light);
    font-size: 20px; line-height: 1;
  }
  .contacts li { display: flex; align-items: center; gap: 9px; margin-top: 8px; }
  .contacts svg { width: 16px; height: 16px; flex: none; }
</style>
</head>
<body>
<main class="sheet">

  <section class="card card-back" aria-label="Card back">
    <div class="wordmark">BELLHAVEN</div>
  </section>

  <section class="card card-front" aria-label="Card front">
    <svg class="front-shape" viewBox="0 0 760 434" aria-hidden="true">
      <path d="M 420 90 A 215 215 0 0 0 640 365" fill="none" stroke="var(--paper-white)" stroke-width="3"/>
      <circle cx="650" cy="145" r="222" fill="var(--paper-white)"/>
    </svg>
    <div class="wordmark">BELLHAVEN</div>

    <div class="identity">
      <div class="person-name">LIORA QUENBY</div>
      <div class="person-title">Chief Financial Officer</div>
    </div>

    <ul class="contacts">
      <li>
        <svg viewBox="0 0 16 16" aria-hidden="true"><path d="M4 1.5 6.2 4 5 5.6c.8 1.9 2.4 3.5 4.4 4.4L11 8.8l2.5 2.2-1.3 2.5C7 13.2 2.8 9 2.5 3.8Z" fill="var(--text-light)"/></svg>
        780-555-0142
      </li>
      <li>
        <svg viewBox="0 0 16 16" aria-hidden="true"><rect x="1" y="3.5" width="14" height="9.5" fill="none" stroke="var(--text-light)" stroke-width="1.6"/><path d="M1.5 4 8 9l6.5-5" fill="none" stroke="var(--text-light)" stroke-width="1.6"/></svg>
        lioraquenby@bellhavengroup.example
      </li>
      <li>
        <svg viewBox="0 0 16 16" aria-hidden="true"><circle cx="8" cy="8" r="6.5" fill="none" stroke="var(--text-light)" stroke-width="1.4"/><ellipse cx="8" cy="8" rx="2.8" ry="6.5" fill="none" stroke="var(--text-light)" stroke-width="1.2"/><path d="M1.5 8h13M2.5 5h11M2.5 11h11" stroke="var(--text-light)" stroke-width="1.1"/></svg>
        www.bellhavengroup.example
      </li>
    </ul>
  </section>

</main>
</body>
</html>
```